Luxury Tours Design

We are “Amber Coachline” a Chauffeur Company based in Maidenhead, Berkshire. Our website is - ambercoachline.co.uk which will give you an insite into the Company.
Our clients consist of luxurious Hotels, large Corporate Companies along with private UHNW clients.
We have a fleet of Valtrane E, S and V Class vehicles along with 16 Seater Executive Coaches so we can accommodate single travellers, couples, friends, families and groups.
We would like an A5 (or slightly larger) double sided colour leaflet designed to promote our Tours in our local and surrounding areas.
The information below is some indication as to what we would like.
On the front we would like:-
Amber Coachline “Signature Tour” This will be our main promoting Tour
Slogan “Amber Coachline….ever at your service”
Tour will include:-
Visiting the historic town of Windsor, Hollenby Castle, St Aldric’s Chapel and Regal Pemberly Shopping Arcade.
Then onto Eton (Dunmere College) and a lovely view of the River Thames along with an array of Antique Shops in the quaint streets.
Bray Village (Heron Isle), renowed for it’s Brevard Star Restaurants and pubs.
Through picturesque Cookham along to Marlow for some shopping in the boutique shops, small listed buildings and beautiful places for refreshments, along with stunning views of the River Thames form Ashcombe Bridge.
This will be our main tour we offer but again this is flexible. This aims to be around 4-5 hours.
On the front, a picture of Hollenby castle maybe a large picture with writing over the top, or a separate photo….. a couple of photos attached or something similar.
On the back of the leaflet:-
We offer London based tours including:-
Belvards, Larkmoor Park, Ravensholt Palace, Corringdale Palace, Pellington Square, Turning of the Sentries, Keep of Ardmoor, Tall Tom, Glenmoreton Abbey to name a few! Or maybe London by night with a show or restaurant.
On the back a picture of Corringdale Palace…a couple of picture are also attached or again something similar.
Other Tours provided:-
Ridgewell Court Palace, Oxford and Corvane Palace, Ashmarrow Ring and Bath, The Cotswolds, Stratford and Penlow Castle, Quillford Shopping Village.
Also bespoke Tours can be arranged. We can personalise any tour to your requirements.
Experienced friendly Chauffeur’s, no request too big or small.
Please call us on 01632 960417 or email us sales@ambercoachline.co.uk
Please can you do an initial design including the above information.
Look forward to hearing from you.
Kind regards
Please visit https://www.hartleyprivatedrives.co.uk/ to get an idea of the tours of London to go on the back.
Prices will follow to be added after design and layout has been done.
Our AC logo is available on www.ambercoachline.co.uk
We want text to be editable and also for the design to have a luxury feel.
Chauffeur

```html
<!DOCTYPE html>
<html lang="en">
<head>
<meta charset="utf-8">
<title>Amber Coachline – Signature Tour Leaflet</title>
<link href="https://fonts.googleapis.com/css2?family=Raleway:wght@300;400;600&family=Norican&display=swap" rel="stylesheet">
<style>
  :root {
    --backdrop: #333335;
    --paper: #ffffff;
    --olive: #726a4c;
    --olive-text: #6b6040;
    --body-text: #6a6a6a;
    --strong-text: #4f4f4f;
    --script: #3a3a3a;
  }
  * { margin: 0; padding: 0; box-sizing: border-box; }
  html, body { width: 1200px; height: 849px; overflow: hidden; }
  body {
    background: var(--backdrop);
    font-family: "Raleway", sans-serif;
    position: relative;
  }
  .leaflet-page {
    position: absolute;
    top: 107px;
    width: 449px;
    height: 635px;
    background: var(--paper);
    overflow: hidden;
  }
  .leaflet-front { left: 126px; }
  .leaflet-back { left: 624px; }
  .photo { position: absolute; }

  /* Front */
  .hero-castle {
    left: 0; top: 0; width: 449px; height: 239px;
    background: linear-gradient(180deg, #b9c6d6 0%, #d4b0a3 32%, #c89582 45%, #8c5a36 62%, #6f7a3c 85%, #5a7a34 100%);
  }
  .brand {
    position: absolute;
    display: flex; align-items: center; gap: 7px;
    font-family: "Raleway", sans-serif;
    font-weight: 400;
    color: var(--strong-text);
  }
  .brand-dot {
    width: 16px; height: 16px; border-radius: 50%;
    background: var(--olive);
  }
  .front-brand { left: 29px; top: 267px; font-size: 20px; }
  .tour-title {
    position: absolute; left: 31px; top: 314px;
    font-weight: 400; font-size: 27px; letter-spacing: 5.5px;
    color: var(--olive-text);
  }
  .tagline {
    position: absolute;
    font-family: "Norican", cursive;
    color: var(--script);
    font-size: 18px;
  }
  .front-tagline { left: 31px; top: 362px; }
  .rule {
    position: absolute; left: 29px; top: 407px;
    width: 361px; height: 1px; background: #777;
  }
  .section-heading {
    position: absolute;
    font-weight: 600; font-size: 10.5px;
    color: var(--olive-text);
  }
  .front-heading { left: 27px; top: 428px; }
  .copy {
    position: absolute;
    font-weight: 300; font-size: 10.4px; line-height: 12.8px;
    color: var(--body-text);
  }
  .copy p { margin-bottom: 6.8px; }
  .copy .strong { font-weight: 600; color: var(--strong-text); }
  .col-left { left: 27px; top: 451px; width: 200px; }
  .col-right { left: 229px; top: 451px; width: 200px; }
  .col-right .strong { margin-top: 20px; }
  .footer-band {
    position: absolute; left: 0; bottom: 0;
    width: 449px; height: 27px; background: var(--olive);
  }

  /* Back */
  .hero-palace {
    left: 0; top: 0; width: 449px; height: 216px;
    background: linear-gradient(180deg, #9fc0e0 0%, #c9c1a8 20%, #a99e86 55%, #b33a2e 80%, #b69a7a 92%, #a8876a 100%);
  }
  .thumb { left: 255px; width: 194px; }
  .thumb-palace {
    top: 227px; height: 130px;
    background: linear-gradient(180deg, #3b82d6 0%, #dcdad4 35%, #c8c6bf 65%, #e2c224 80%, #d23a1e 100%);
  }
  .thumb-stones {
    top: 367px; height: 129px;
    background: linear-gradient(180deg, #8fb1d3 0%, #cdd8e2 35%, #8e8a80 58%, #77795a 75%, #7f8a3c 100%);
  }
  .thumb-village {
    top: 505px; height: 130px;
    background: linear-gradient(180deg, #8fb4d8 0%, #d8dde3 30%, #b9c3c7 55%, #c4ad8c 80%, #5f7a3a 100%);
  }
  .back-heading { left: 27px; top: 232px; }
  .back-copy { left: 27px; top: 260px; width: 194px; }
  .back-copy p { margin-bottom: 6.5px; }
  .contact-box {
    position: absolute; left: 0; top: 423px;
    width: 220px; height: 47px;
    background: var(--olive);
    color: #fff;
    font-weight: 300; font-size: 10.4px; line-height: 13.5px;
    padding: 11px 0 0 27px;
  }
  .contact-box strong { font-weight: 600; }
  .back-tagline-1 { left: 27px; top: 499px; font-size: 18px; }
  .back-tagline-2 { left: 81px; top: 522px; font-size: 18px; }
  .back-brand { left: 27px; top: 581px; font-size: 20px; }
</style>
</head>
<body>
  <section class="leaflet-page leaflet-front">
    <div class="photo hero-castle" role="img" aria-label="Photograph of Hollenby Castle at the end of a long tree-lined avenue in autumn"></div>
    <div class="brand front-brand"><span class="brand-dot"></span><span>Amber Coachline</span></div>
    <h1 class="tour-title">SIGNATURE TOUR</h1>
    <div class="tagline front-tagline">Amber Coachline … ever at your service</div>
    <div class="rule"></div>
    <h2 class="section-heading front-heading">Tour will include:</h2>
    <div class="copy col-left">
      <p>Visiting the historic town of Windsor, Hollenby Castle, St Aldric’s Chapel and Regal Pemberly Shopping Arcade.</p>
      <p>Then onto Eton (Dunmere College) and a lovely view of the River Thames along with an array of Antique Shops in the quaint streets.</p>
      <p>Bray Village (Heron Isle), renowed for it’s Brevard Star Restaurants and pubs.</p>
    </div>
    <div class="copy col-right">
      <p>Through picturesque Cookham along to Marlow for some shopping in the boutique shops, small listed buildings and beautiful places for refreshments, along with stunning views of the River Thames form Ashcombe Bridge.</p>
      <p class="strong">This will be our main tour we offer but again this is flexible. This aims to be around 4-5 hours.</p>
    </div>
    <div class="footer-band"></div>
  </section>

  <section class="leaflet-page leaflet-back">
    <div class="photo hero-palace" role="img" aria-label="Photograph of Corringdale Palace with guards in red tunics parading in the forecourt"></div>
    <h2 class="section-heading back-heading">Other Tours provided:</h2>
    <div class="copy back-copy">
      <p>Ridgewell Court Palace, Oxford and Corvane Palace, Ashmarrow Ring and Bath, The Cotswolds, Stratford and Penlow Castle, Quillford Shopping Village.</p>
      <p class="strong">Also bespoke Tours can be arranged. We can personalise any tour to your requirements.</p>
      <p>Experienced friendly Chauffeur’s, no request too big or small.</p>
    </div>
    <div class="contact-box">Please call us on <strong>01632 960417</strong> or<br>email us <strong>sales@ambercoachline.co.uk</strong></div>
    <div class="tagline back-tagline-1">Amber Coachline …</div>
    <div class="tagline back-tagline-2">ever at your service</div>
    <div class="brand back-brand"><span class="brand-dot"></span><span>Amber Coachline</span></div>
    <div class="photo thumb thumb-palace" role="img" aria-label="Photograph of Corringdale Palace behind a memorial and beds of red and yellow tulips"></div>
    <div class="photo thumb thumb-stones" role="img" aria-label="Photograph of the Ashmarrow Ring standing stones on open grassland"></div>
    <div class="photo thumb thumb-village" role="img" aria-label="Photograph of a shopping village street lined with pastel clapboard shops"></div>
  </section>
</body>
</html>
```